kelvaro stationary business card and letterhead

THIS PROJECT IS TO DESIGN A BUSINESS CARD DOUBLE SIDES .

Reason: I AM WAITING FOR TESINU SUBMISION

Industry/Entity Type

Business

Font styles to use
Other font styles liked:
• Chose your font

```html
<!DOCTYPE html>
<html lang="en">
<head>
<meta charset="utf-8">
<title>Kelvaro business card</title>
<link rel="stylesheet" href="https://fonts.googleapis.com/css2?family=Questrial&display=swap">
<style>
  :root {
    --backdrop: #8c8c8a;
    --card-black: #050505;
    --accent-yellow: #d9a90f;
    --ink-white: #f2f2ee;
    --rule-white: #e8e8e8;
  }
  html, body {
    margin: 0;
    padding: 0;
    width: 1200px;
    height: 1000px;
    overflow: hidden;
    background: var(--backdrop);
    font-family: "Questrial", "Century Gothic", sans-serif;
  }
  .stage {
    position: relative;
    width: 1200px;
    height: 1000px;
  }
  .card {
    position: absolute;
    left: 300px;
    width: 600px;
    height: 343px;
    background: var(--card-black);
    box-shadow: 0 6px 18px rgba(0,0,0,0.25);
    overflow: hidden;
  }
  .card--back { top: 100px; }
  .card--front { top: 557px; }

  /* back side */
  .back-mark {
    position: absolute;
    left: 50%;
    top: 50%;
    transform: translate(-50%, -50%);
    display: flex;
    align-items: center;
    gap: 22px;
  }
  .back-mark .dot {
    width: 86px;
    height: 86px;
    border-radius: 50%;
    background: var(--accent-yellow);
  }
  .back-mark .name {
    color: var(--ink-white);
    font-size: 64px;
    letter-spacing: 1px;
  }

  /* front side */
  .brand {
    position: absolute;
    left: 42px;
    top: 128px;
  }
  .brand-row {
    display: flex;
    align-items: center;
    gap: 10px;
  }
  .brand .dot {
    width: 40px;
    height: 40px;
    border-radius: 50%;
    background: var(--accent-yellow);
  }
  .brand .name {
    color: var(--ink-white);
    font-size: 44px;
    line-height: 1;
  }
  .brand .tagline {
    margin: 4px 0 0 50px;
    color: var(--accent-yellow);
    font-size: 9px;
    letter-spacing: 5.2px;
    text-transform: uppercase;
  }
  .contact {
    position: absolute;
    left: 368px;
    top: 150px;
  }
</style>
</head>
<body>
<main class="stage">

  <section class="card card--back" aria-label="Card back">
    <div class="back-mark">
      <span class="dot"></span>
      <span class="name">Kelvaro</span>
    </div>
  </section>

  <section class="card card--front" aria-label="Card front">
    <div class="brand">
      <div class="brand-row">
        <span class="dot"></span>
        <span class="name">Kelvaro</span>
      </div>
      <div class="tagline">International Consulting</div>
    </div>

    <svg class="contact" width="210" height="110" viewBox="0 0 210 110" aria-label="Contact fields">
      <g stroke="var(--rule-white)" stroke-width="1.3" fill="none">
        <line x1="42" y1="0" x2="42" y2="104"/>
        <line x1="0" y1="18" x2="206" y2="30"/>
        <line x1="0" y1="38" x2="204" y2="50"/>
        <line x1="0" y1="58" x2="202" y2="70"/>
        <line x1="0" y1="78" x2="200" y2="90"/>
      </g>
      <g fill="var(--ink-white)">
        <!-- person -->
        <circle cx="34" cy="5" r="3"/>
        <path d="M28 14 q6 -8 12 0 z"/>
        <!-- phone -->
        <path d="M29 22 l3 0 l1 3 l-2 1 q1 3 4 4 l1 -2 l3 1 l0 3 q-9 0 -10 -10 z"/>
        <!-- mail -->
        <rect x="28" y="43" width="12" height="9"/>
        <path d="M28 43 l6 5 l6 -5" stroke="var(--card-black)" stroke-width="1" fill="none"/>
        <!-- home -->
        <path d="M27 68 l7 -6 l7 6 l-2 0 l0 5 l-10 0 l0 -5 z"/>
        <!-- globe -->
        <circle cx="32" cy="89" r="6"/>
        <g stroke="var(--card-black)" stroke-width="0.8" fill="none">
          <ellipse cx="32" cy="89" rx="2.5" ry="6"/>
          <line x1="26" y1="89" x2="38" y2="89"/>
        </g>
      </g>
    </svg>
  </section>

</main>
</body>
</html>
```